Family business needs stationery redesign with new logo

Family owned company, established in 1987 wanting a brand 'refresh'. We are an electrical, refrigeration and construction company based in the Barkly Region Northern Territory, Australia. We have a new logo we would like to use which is uploaded along with our current letterhead and email signature. We are also dropping the word 'contractors' so please do not include this on any designs. Please note also, the 'orange' color used in our logo and designs should be Northern Territory red ochre which is as follows:

RGB (Hex): #C75B12
PantoneĀ® 159 C
CMYK: 1 / 74 / 100 / 7

We are needing our stationery redesigned using our new logo. Please include letterheads, business cards, envelopes, and email signatures.

We currently use our business letterheads for quotations, invoices, letters, HR matters, and internal memos.

We also need a separate simplified letterhead for internal paperwork such as employee leave forms, meeting agendas, and meeting minutes etc.

Reason: Needing more submissions of full package designs. We are wanting all our stationery, including business cards, letterheads, email signatures, envelopes, etc to be cohesive. We also require ALL the information, as supplied on our template letterhead, to be included on the new letterhead designs. including electrical license no.etc Thank you, R&W

Reason: needing more time as work has got in the way of looking over designs. A lot of designs not meeting the brief/criteria.

Industry/Entity Type

Business

Colors
0355a3
f37122

Requirements
Must have
• The 'orange' color used in the designs should be Northern Territory red ochre which is as follows:
• RGB (Hex): #C75B12
• PantoneĀ® 159 C
• CMYK: 1 / 74 / 100 / 7
• ***MUST INCLUDE ALL INFORMATION THAT IS ON OUR CURRENT LETTERHEAD***
Should not have
• Please do not include the word 'contractors'

```html
<!DOCTYPE html>
<html lang="en">
<head>
<meta charset="utf-8">
<title>R&amp;W Letterhead</title>
<link href="https://fonts.googleapis.com/css2?family=Arimo:wght@400;700&display=swap" rel="stylesheet">
<style>
  :root {
    --backdrop: #e6e6e6;
    --paper: #ffffff;
    --navy: #1c2a6e;
    --ochre: #c75b12;
    --ochre-bright: #e8561c;
    --rule-grey: #d9dbdf;
    --text-grey: #8a8c90;
    --watermark: #f3f3f3;
  }
  * { margin: 0; padding: 0; box-sizing: border-box; }
  html, body {
    width: 1200px; height: 784px; overflow: hidden;
    background: var(--backdrop);
    font-family: "Arimo", Arial, sans-serif;
  }
  .letterhead {
    position: absolute; left: 340px; top: 24px;
    width: 520px; height: 736px;
    background: var(--paper);
    box-shadow: 0 2px 8px rgba(0,0,0,0.12);
    overflow: hidden;
  }
  .edge-rule {
    position: absolute; top: 0; width: 3px; height: 100%;
    background: var(--rule-grey);
  }
  .edge-rule--left { left: 0; }
  .edge-rule--right { right: 0; }
  .accent-bar {
    position: absolute; width: 7px; height: 205px;
    background: linear-gradient(180deg, var(--ochre), var(--ochre-bright));
  }
  .accent-bar--right { right: 0; top: 150px; }
  .accent-bar--left { left: 0; top: 470px; }
  .brand {
    position: absolute; left: 34px; top: 28px;
  }
  .brand-mark { display: flex; align-items: center; gap: 10px; }
  .brand-dot {
    width: 14px; height: 14px; border-radius: 50%;
    background: var(--ochre);
  }
  .brand-name {
    font-weight: 700; font-size: 40px; color: var(--navy);
    letter-spacing: 1px; line-height: 1;
  }
  .brand-services {
    margin-top: 8px; font-size: 8.5px; color: var(--text-grey);
    letter-spacing: 0.2px;
  }
  .brand-services .divider { color: var(--ochre); padding: 0 3px; }
  .contact {
    position: absolute; right: 34px; top: 92px;
    font-size: 8.5px; font-style: normal; color: var(--text-grey);
    line-height: 14px;
  }
  .contact-line { display: flex; align-items: center; gap: 6px; white-space: nowrap; }
  .contact-item { display: inline-flex; align-items: center; gap: 3px; }
  .icon {
    display: inline-flex; align-items: center; justify-content: center;
    width: 9px; height: 9px; border-radius: 50%;
    background: var(--ochre); color: #fff;
    font-size: 5.5px; font-weight: 700;
  }
  .watermark {
    position: absolute; left: 30px; top: 480px;
    font-weight: 700; font-size: 140px; color: var(--watermark);
    line-height: 1; letter-spacing: 2px;
  }
</style>
</head>
<body>
  <main class="letterhead">
    <div class="edge-rule edge-rule--left"></div>
    <div class="edge-rule edge-rule--right"></div>
    <div class="accent-bar accent-bar--right"></div>
    <div class="accent-bar accent-bar--left"></div>

    <header class="brand">
      <div class="brand-mark">
        <span class="brand-dot"></span>
        <span class="brand-name">R&amp;W</span>
      </div>
      <div class="brand-services">Electrical<span class="divider">|</span>Refrigeration<span class="divider">|</span>Building Services</div>
    </header>

    <address class="contact">
      <div class="contact-line">
        <span class="contact-item"><span class="icon">P</span>PO Box 2210 | 42 Ridgeway Rd, Redgum Flat NT 0800</span>
      </div>
      <div class="contact-line">
        <span class="contact-item"><span class="icon">T</span>08 8100 0000</span>
        <span class="contact-item"><span class="icon">M</span>0400 000 000</span>
        <span class="contact-item"><span class="icon">F</span>08 8100 0000</span>
      </div>
      <div class="contact-line">
        <span class="contact-item"><span class="icon">E</span>hello@rwservices.com.au</span>
        <span class="contact-item"><span class="icon">W</span>www.rwservices.com.au</span>
      </div>
      <div class="contact-line">
        <span class="contact-item"><span class="icon">L</span>Electrical Licence No. E00000</span>
      </div>
    </address>

    <div class="watermark" aria-hidden="true">R&amp;W</div>
  </main>
</body>
</html>
```